Brickfield real estate investment company needs a poster design

We would like a poster design size 18 x 24.
Poster wording -
I WANT TO BUY YOUR ( finish with logo) logo uploaded
website- www.brickfield.example
phone # 555-218-7043 ( color red for the phone number)
we would like to see the poster on 2 different backgrounds
Yellow background
White background
horizontal

```html
<!DOCTYPE html>
<html lang="en">
<head>
<meta charset="utf-8">
<title>Brickfield – I Want To Buy Your House</title>
<link rel="stylesheet" href="https://fonts.googleapis.com/css2?family=Anton&family=Montserrat:wght@700;800&display=swap">
<style>
  :root {
    --ink: #0b0b0b;
    --sun: #ffe55c;
    --sun-deep: #f5d63e;
    --alert-red: #e5222b;
  }
  * { margin: 0; padding: 0; box-sizing: border-box; }
  html, body { width: 1200px; height: 900px; overflow: hidden; background: var(--ink); }
  .poster {
    position: relative;
    width: 1200px;
    height: 900px;
    overflow: hidden;
    background: var(--sun);
  }
  .band {
    position: absolute;
    left: 0;
    width: 1200px;
    background: var(--ink);
    display: flex;
    align-items: center;
    justify-content: center;
  }
  .band--top { top: 0; height: 102px; }
  .band--bottom { top: 796px; height: 104px; }
  .website {
    font-family: "Montserrat", sans-serif;
    font-weight: 700;
    font-size: 44px;
    color: var(--sun);
    letter-spacing: 27px;
    padding-left: 27px;
    white-space: nowrap;
  }
  .burst {
    position: absolute;
    top: 102px;
    left: 0;
    width: 1200px;
    height: 694px;
    background: radial-gradient(ellipse at 50% 50%, var(--sun) 0%, var(--sun) 45%, var(--sun-deep) 100%);
  }
  .headline {
    position: absolute;
    top: 186px;
    left: 0;
    width: 1200px;
    text-align: center;
    font-family: "Anton", sans-serif;
    font-weight: 400;
    font-size: 122px;
    line-height: 124px;
    color: var(--ink);
    text-transform: uppercase;
  }
  .headline span {
    display: block;
    height: 124px;
    transform: scaleX(1.2);
  }
  .brand {
    position: absolute;
    top: 605px;
    left: 0;
    width: 1200px;
    display: flex;
    align-items: center;
    justify-content: center;
  }
  .brand__name {
    font-family: "Anton", sans-serif;
    font-size: 100px;
    line-height: 1.2;
    color: var(--ink);
    text-transform: uppercase;
    letter-spacing: 12px;
    padding-left: 12px;
  }
  .phone {
    display: flex;
    align-items: center;
    gap: 36px;
    color: var(--alert-red);
  }
  .phone__icon { width: 70px; height: 70px; display: block; }
  .phone__number {
    font-family: "Montserrat", sans-serif;
    font-weight: 800;
    font-size: 62px;
    letter-spacing: 27px;
    white-space: nowrap;
  }
</style>
</head>
<body>
  <main class="poster">
    <header class="band band--top">
      <p class="website">www.brickfield.example</p>
    </header>

    <div class="burst" role="img" aria-label="Radiating yellow sunburst lines with a faint house outline behind the headline"></div>

    <h1 class="headline">
      <span>I Want</span>
      <span>To Buy</span>
      <span>Your</span>
    </h1>

    <div class="brand">
      <span class="brand__name">Brickfield</span>
    </div>

    <footer class="band band--bottom">
      <div class="phone">
        <svg class="phone__icon" viewBox="0 0 70 70" aria-hidden="true">
          <circle cx="35" cy="35" r="31" fill="none" stroke="currentColor" stroke-width="5"/>
          <path d="M24 19c2-1 4 0 5 2l3 6c1 2 0 3-1 4l-2 2c2 5 6 9 11 11l2-2c1-1 2-2 4-1l6 3c2 1 3 3 2 5l-2 4c-1 2-3 3-6 2-13-4-22-13-26-26-1-3 0-5 2-6z" fill="currentColor"/>
        </svg>
        <p class="phone__number">555-218-7043</p>
      </div>
    </footer>
  </main>
</body>
</html>
```